MV Decor

There is a sample provided with the arabic text of the business card. please copy paste the same text and the same Logo (The two triangles) Just try to incorproate the Brown background attached (you are free to change the colors) Id like the colors to be mainly shades of black and red.

```html
<!DOCTYPE html>
<html lang="ar">
<head>
<meta charset="utf-8">
<title>MV Decor – Business Card</title>
<link rel="stylesheet" href="https://fonts.googleapis.com/css2?family=Tajawal:wght@400;500;700&family=Aref+Ruqaa:wght@400;700&display=swap">
<style>
  :root {
    --page-bg: #ecebe8;
    --card-red: #c8203f;
    --card-red-light: #d9355a;
    --card-red-deep: #b0183a;
    --ink-dark: #252622;
    --ink-light: #ffffff;
    --mark-light: #ebebeb;
  }
  * { margin: 0; padding: 0; box-sizing: border-box; }
  html, body {
    width: 1125px; height: 1200px; overflow: hidden;
    background: var(--page-bg);
  }
  .canvas { position: relative; width: 1125px; height: 1200px; }

  .card {
    position: absolute; left: 170px;
    width: 826px; height: 472px;
    background: var(--card-red);
    overflow: hidden;
    color: var(--ink-light);
    font-family: "Tajawal", sans-serif;
    box-shadow: 0 3px 8px rgba(0,0,0,.25);
  }
  .card--front { top: 106px; }
  .card--back  { top: 640px; }

  .card__texture {
    position: absolute; inset: 0;
    background:
      radial-gradient(ellipse 45% 55% at 55% 30%, var(--card-red-light), transparent 70%),
      radial-gradient(ellipse 50% 40% at 30% 85%, var(--card-red-deep), transparent 70%),
      linear-gradient(160deg, var(--card-red-light), var(--card-red) 55%, var(--card-red-deep));
    opacity: .85;
  }

  .card__corner { position: absolute; left: 0; top: 0; width: 268px; height: 245px; }

  .brand-name {
    position: absolute;
    font-family: "Tajawal", sans-serif;
    font-weight: 700;
    color: var(--ink-light);
    letter-spacing: 2px;
    white-space: nowrap;
    transform: translateX(-50%);
    direction: ltr;
  }
  .card--front .brand-name { left: 232px; top: 345px; font-size: 44px; }
  .card--back .brand-name  { left: 250px; top: 200px; font-size: 58px; }

  .owner {
    position: absolute; right: 55px; top: 66px;
    direction: rtl; text-align: right;
    font-family: "Aref Ruqaa", serif;
  }
  .owner__name { font-size: 30px; font-weight: 700; line-height: 1.2; }
  .owner__title { font-size: 19px; line-height: 1.3; margin-right: 60px; }

  .credentials {
    position: absolute; right: 55px; top: 238px;
    direction: rtl; text-align: right;
    list-style: none;
    font-size: 20px; line-height: 27px; font-weight: 500;
  }

  .phone {
    position: absolute; right: 55px; top: 364px;
    display: flex; align-items: center; gap: 7px;
    font-size: 21px; font-weight: 500; direction: ltr;
  }
  .phone svg { width: 18px; height: 18px; }

  .credentials--bulleted {
    right: 114px; top: 104px;
    font-size: 25px; line-height: 33px;
  }
  .credentials--bulleted li { display: flex; align-items: center; gap: 10px; }
  .bullet {
    width: 8px; height: 8px; border-radius: 50%;
    background: var(--ink-light); flex: none;
  }
</style>
</head>
<body>
<main class="canvas">

  <section class="card card--front">
    <div class="card__texture" role="img" aria-label="Soft red mosaic texture of small squares and circles"></div>
    <svg class="card__corner" viewBox="0 0 268 245" aria-hidden="true">
      <polygon points="0,0 268,0 0,245" fill="var(--ink-dark)"/>
    </svg>

    <div class="brand-name">MV DECOR</div>

    <div class="owner">
      <p class="owner__name">المهندس / سالم ناصر الحداد</p>
      <p class="owner__title">أستاذ جامعي</p>
    </div>

    <ul class="credentials">
      <li>ماجستير هندسة ديكور</li>
      <li>دبلوم عالي فن تشكيلي</li>
      <li>جامعة الفنون (ليون)</li>
      <li>استشارات هندسية - فنية</li>
    </ul>

    <p class="phone">
      <svg viewBox="0 0 24 24" aria-hidden="true"><path fill="var(--ink-light)" d="M6.6 10.8a15.1 15.1 0 0 0 6.6 6.6l2.2-2.2a1 1 0 0 1 1-.25 11.4 11.4 0 0 0 3.6.57 1 1 0 0 1 1 1V20a1 1 0 0 1-1 1A17 17 0 0 1 3 4a1 1 0 0 1 1-1h3.5a1 1 0 0 1 1 1c0 1.25.2 2.45.57 3.57a1 1 0 0 1-.25 1z"/></svg>
      <span>34520917 / 66210458</span>
    </p>
  </section>

  <section class="card card--back">
    <div class="card__texture" role="img" aria-label="Soft red mosaic texture of small squares and circles"></div>

    <div class="brand-name">MV DECOR</div>

    <ul class="credentials credentials--bulleted">
      <li>ماجستير هندسة ديكور<span class="bullet"></span></li>
      <li>دبلوم عالي فن تشكيلي<span class="bullet"></span></li>
      <li>جامعة الفنون (ليون)<span class="bullet"></span></li>
      <li>استشارات هندسية - فنية<span class="bullet"></span></li>
      <li>ماجستير هندسة ديكور<span class="bullet"></span></li>
      <li>دبلوم عالي فن تشكيلي<span class="bullet"></span></li>
      <li>جامعة الفنون (ليون)<span class="bullet"></span></li>
      <li>استشارات هندسية - فنية<span class="bullet"></span></li>
    </ul>
  </section>

</main>
</body>
</html>
```